Business Card Design

New business card design

Target Market(s)

Residential & Commercial Property Managers

Industry/Entity Type

Plumbing Services

Contact Information for Business Card

Name - Rowan Keddle, title - Director, Phone Number - 0431 286 517, email - rowan@tbk-plumbing.com.au, Company ABN - 73 215 904 386,

Font styles to use
Sans Serif

Colors
0054AA
0677BA
7BADD7
CADEEF
E8F1F8

```html
<!DOCTYPE html>
<html lang="en">
<head>
<meta charset="utf-8">
<title>TBK Plumbing Services – Business Card</title>
<link href="https://fonts.googleapis.com/css2?family=Montserrat:wght@300;400;500;700&display=swap" rel="stylesheet">
<style>
  :root {
    --stage: #3a3a3c;
    --card-dark: #1d232a;
    --card-dark-2: #2b343d;
    --card-light: #ffffff;
    --ink: #1a1d21;
    --ink-soft: #4a4e54;
    --accent: #1aa3e8;
    --rule: #c9ccd0;
    --logo-ink: #ffffff;
    --tag-ink: #c7ccd2;
  }
  * { box-sizing: border-box; margin: 0; padding: 0; }
  html, body {
    width: 1200px; height: 689px; overflow: hidden;
    background: var(--stage);
    font-family: "Montserrat", Arial, sans-serif;
  }
  .stage {
    position: relative; width: 1200px; height: 689px;
    display: flex; align-items: center; justify-content: center; gap: 60px;
  }
  .card {
    position: relative; width: 500px; height: 286px;
    border-radius: 18px; overflow: hidden;
    box-shadow: 0 18px 40px rgba(0,0,0,.45);
  }
  /* front */
  .card--front { background: var(--card-dark); }
  .card__pattern {
    position: absolute; inset: 0;
    background: radial-gradient(ellipse at 75% 20%, var(--card-dark-2), var(--card-dark) 70%);
  }
  .brand {
    position: absolute; left: 0; right: 0; top: 92px;
    display: flex; flex-direction: column; align-items: center;
  }
  .brand__name {
    display: flex; align-items: center; gap: 12px;
    color: var(--logo-ink); font-weight: 300; font-size: 78px;
    letter-spacing: 2px; line-height: 1;
  }
  .brand__dot {
    width: 14px; height: 14px; border-radius: 50%; background: var(--accent);
  }
  .brand__tagline {
    margin-top: 16px; color: var(--tag-ink); font-weight: 300;
    font-size: 11px; letter-spacing: 9px; text-transform: lowercase;
  }
  /* back */
  .card--back { background: var(--card-light); }
  .contact {
    position: absolute; left: 0; right: 0; top: 0; bottom: 0;
    display: flex; align-items: center; justify-content: center;
  }
  .contact__person { text-align: right; padding-right: 18px; }
  .contact__name { color: var(--ink); font-weight: 700; font-size: 22px; letter-spacing: -.3px; }
  .contact__title { color: var(--accent); font-weight: 400; font-size: 13px; margin-top: 2px; }
  .contact__rule { width: 1px; height: 66px; background: var(--rule); }
  .contact__details {
    padding-left: 18px; list-style: none;
    color: var(--ink-soft); font-size: 12.5px; line-height: 1.6;
  }
  .contact__details li { display: flex; align-items: center; gap: 7px; }
  .contact__details svg { width: 12px; height: 12px; fill: var(--ink); flex: none; }
</style>
</head>
<body>
<main class="stage">
  <section class="card card--front">
    <div class="card__pattern" role="img" aria-label="Repeating embossed water-drop pattern across the card"></div>
    <div class="brand">
      <div class="brand__name">tbk<span class="brand__dot"></span></div>
      <div class="brand__tagline">plumbing services</div>
    </div>
  </section>

  <section class="card card--back">
    <div class="contact">
      <div class="contact__person">
        <div class="contact__name">Rowan Keddle</div>
        <div class="contact__title">Director</div>
      </div>
      <div class="contact__rule"></div>
      <ul class="contact__details">
        <li>ABN - 73 215 904 386</li>
        <li>
          <svg viewBox="0 0 24 24" aria-hidden="true"><path d="M6.6 10.8a15.1 15.1 0 0 0 6.6 6.6l2.2-2.2c.3-.3.7-.4 1-.2 1.1.4 2.3.6 3.6.6.6 0 1 .4 1 1V20c0 .6-.4 1-1 1A17 17 0 0 1 3 4c0-.6.4-1 1-1h3.5c.6 0 1 .4 1 1 0 1.3.2 2.5.6 3.6.1.3 0 .7-.2 1z"/></svg>
          0431 286 517
        </li>
        <li>
          <svg viewBox="0 0 24 24" aria-hidden="true"><path d="M2 5h20v14H2z M3.5 6.5 12 13l8.5-6.5" fill="none" stroke="#1a1d21" stroke-width="2"/><path d="M2 5h20L12 12z"/></svg>
          rowan@tbk-plumbing.com.au
        </li>
      </ul>
    </div>
  </section>
</main>
</body>
</html>
```